VELQUINT

1. My company will allow people to buy either stock made or custom scented aromatherapy candles, lotions,soaps,body sprays, and wax melts. As there isn't a company that allows for custom oil scent mixes but me. We are just starting with the candles and the other items will be coming later.

2. My target audience is anyone who would want to buy my product. It isn't really limited due to the nature of the product I will be providing.

3. velquint.com is the domain name (purchased from plorvex.com).

4. So what I really need is the shopping cart function. A fully coded shopping cart that will calculate shipping and sales tax if need be. I need the cart function to be just like every other major retailers shopping cart function. So they can click on an item they want and have it go into a shopping cart for the customer to then be able to go and pay for their goods. I also need help creating single pages for each product. So that each thing we make has a separate page with a description and an add to cart button.

5. I would like the color scheme to follow the logo I made. I would also like the logo top center of first page. I would like the quote " elevate your choices in aromatherapy products"

^. I basically need a checkout just like every other good website. A clear shipping area for them to populate, sales tax calculator, ya know everything a normal checkout has like tressly or dunvexa.com. I also have a vonk account already as well.

```html
<!DOCTYPE html>
<html lang="en">
<head>
<meta charset="utf-8">
<title>Velquint – Aromatherapy Products</title>
<link rel="stylesheet" href="https://fonts.googleapis.com/css2?family=Montserrat:wght@600;700;800&family=Poppins:wght@300;400;500;600;700&display=swap">
<style>
:root{
  --purple:#6a2fd0;
  --purple-deep:#4b1ea6;
  --purple-soft:#e6dcf7;
  --blue:#2b9df0;
  --ink:#111111;
  --dark:#1b1b1d;
  --grey-bg:#e4e3e6;
  --muted:#6d6d6d;
  --white:#ffffff;
  --star:#f2a516;
}
*{box-sizing:border-box;margin:0;padding:0}
html,body{width:1200px;height:4566px;overflow:hidden}
body{position:relative;background:var(--white);font-family:'Poppins',sans-serif;color:var(--ink)}
.abs{position:absolute}
a{color:inherit;text-decoration:none}
.heading{font-family:'Montserrat',sans-serif;font-weight:800;letter-spacing:1px;text-align:center;position:absolute;left:0;width:1200px;font-size:38px;line-height:1}
.btn{position:absolute;display:flex;align-items:center;justify-content:center;border-radius:26px;background:var(--purple);color:var(--white);font-family:'Montserrat',sans-serif;font-weight:700;font-size:15px;letter-spacing:.3px}

.topbar{left:0;top:0;width:1200px;height:43px;background:#000;color:var(--white);font-size:12px}
.topbar span{position:absolute;top:15px}
.navbar{left:0;top:43px;width:1200px;height:85px;background:var(--dark);color:var(--white);font-size:14px}
.navbar .link{position:absolute;top:29px}
.navbar .active{color:#8fb8ff;text-decoration:underline;text-underline-offset:4px}
.brand-badge{left:510px;top:0;width:180px;height:186px;border-radius:50%;background:#000;display:flex;align-items:center;justify-content:center;flex-direction:column;color:#b89af2;font-family:'Montserrat',sans-serif;font-weight:700;font-size:19px;letter-spacing:2px}
.brand-badge i{display:block;width:58px;height:58px;border-radius:50%;background:var(--purple);margin-bottom:10px}

.hero-photo{left:0;top:128px;width:1200px;height:560px;background:radial-gradient(ellipse at 50% 40%,#d9d5dc 0%,#bdb8c0 55%,#9d96a3 100%)}
.hero-title{left:0;top:240px;width:1200px;text-align:center;font-family:'Montserrat',sans-serif;font-weight:700;font-size:39px;line-height:48px;letter-spacing:1px;color:var(--ink)}
.hero-sub{left:0;top:348px;width:1200px;text-align:center;font-size:17px;line-height:30px;color:#222}

.cat{position:absolute;top:780px;width:306px;height:223px;border-radius:6px;overflow:hidden;background:linear-gradient(100deg,#4a4550 0%,#8f8a90 55%,#d6d1cf 100%);color:var(--white)}
.cat h3{position:absolute;left:20px;top:32px;font-size:20px;font-weight:600}
.cat p{position:absolute;left:20px;top:62px;width:190px;font-size:13px;line-height:26px}
.cat .btn{left:20px;top:152px;width:158px;height:45px;font-size:15px;background:var(--purple)}
.soon{position:absolute;left:64px;top:83px;width:179px;height:45px;border-radius:10px;background:var(--white);color:var(--ink);display:flex;align-items:center;justify-content:center;font-size:19px;font-weight:600;box-shadow:0 2px 8px rgba(0,0,0,.25)}
.arrow{position:absolute;width:38px;height:38px;border-radius:50%;border:2px solid #222;background:var(--white);display:flex;align-items:center;justify-content:center}
.arrow.next{border-color:var(--purple)}

.product{position:absolute;top:1172px;width:296px}
.product .photo{width:296px;height:320px;border-radius:8px;background:linear-gradient(160deg,#efe7df 0%,#d8ccc0 60%,#b9aa9b 100%)}
.product .label{position:absolute;left:23px;top:267px;width:250px;height:53px;background:var(--white);border-radius:8px 8px 0 0;text-align:center;font-weight:600;font-size:19px;padding-top:14px}
.product .icon{position:absolute;left:240px;width:38px;height:38px;border-radius:50%;background:var(--white);display:flex;align-items:center;justify-content:center}
.stars{color:var(--star);font-size:14px;letter-spacing:1px}
.product .stars{position:absolute;top:313px;left:0;width:296px;text-align:center}
.product .price{position:absolute;top:336px;left:0;width:296px;text-align:center;font-size:21px}
.product .price s{font-size:13px;color:#444;margin-right:6px}
.product .btn{top:377px;left:76px;width:159px;height:48px}

.custom-bg{left:0;top:1684px;width:1200px;height:568px}
.custom-title{left:110px;top:1796px;font-family:'Montserrat',sans-serif;font-weight:800;font-size:42px;line-height:53px;letter-spacing:1px}
.custom-text{left:112px;top:1908px;width:420px;font-size:13.5px;line-height:27.5px;color:#222}

.benefit{position:absolute;top:2403px;width:235px;height:284px;background:var(--white);box-shadow:0 2px 10px rgba(0,0,0,.18);text-align:center}
.benefit .ico{width:92px;height:92px;border-radius:50%;background:var(--purple-soft);margin:20px auto 0;display:flex;align-items:center;justify-content:center}
.benefit h4{margin-top:26px;font-size:19px;font-weight:600}
.benefit p{margin-top:14px;font-size:14px;line-height:28px;color:var(--muted);padding:0 22px}

.review{position:absolute;top:2841px;width:310px;height:300px;background:var(--white);box-shadow:0 2px 10px rgba(0,0,0,.16)}
.review p{position:absolute;left:23px;top:34px;width:270px;font-size:14px;line-height:28.5px;color:var(--muted)}
.review hr{position:absolute;left:23px;top:167px;width:265px;border:0;border-top:1px solid #b9b9b9}
.avatar{position:absolute;left:12px;top:185px;width:92px;height:92px;border-radius:50%;background:linear-gradient(160deg,#cfd6dc,#8c99a4)}
.review .name{position:absolute;left:120px;top:196px;font-size:18px;font-weight:600;color:var(--purple-deep)}
.review .role{position:absolute;left:120px;top:227px;font-size:15px;color:#444}
.review .stars{position:absolute;left:120px;top:256px}
.review .src{position:absolute;left:246px;top:220px;font-size:14px;font-weight:600;color:var(--ink)}
.dot{position:absolute;top:3196px;width:13px;height:13px;border-radius:50%;background:#bdbdbd}

.follow-bg{left:0;top:3300px;width:1200px;height:590px}
.follow-title{left:0;top:3380px;width:1200px;text-align:center;color:var(--white);font-family:'Montserrat',sans-serif;font-weight:800;font-size:38px;letter-spacing:2px}
.shot{position:absolute;top:3463px;height:282px}

.footer{left:0;top:3882px;width:1200px;height:684px;background:#000;color:var(--white)}
.news-title{left:0;top:3990px;width:1200px;text-align:center;font-size:38px;font-weight:500;color:var(--white)}
.field{position:absolute;top:4077px;height:46px;border-radius:23px;background:var(--white);color:#222;font-size:16px;padding:12px 20px}
.rule{position:absolute;left:110px;width:978px;border-top:1px solid #555}
.col-title{position:absolute;top:4237px;font-size:17px;font-weight:500;color:var(--white)}
.col-link{position:absolute;font-size:14px;color:var(--white)}
.col-link b{font-weight:700;margin-right:10px}
.social{position:absolute;top:4403px;width:28px;height:28px;border-radius:50%;background:var(--white)}
.pay{position:absolute;top:4516px;width:33px;height:22px;border-radius:3px;background:#e9e9ef}
</style>
</head>
<body>

<div class="abs topbar">
  <span style="left:112px">About Us</span>
  <span style="left:209px">Contact Us</span>
  <span style="left:326px">Customize Your Product</span>
  <span style="left:847px">Customer Care: info@velquint.com</span>
</div>

<nav class="abs navbar">
  <a class="link active" style="left:112px">Home</a>
  <a class="link" style="left:193px">Candles</a>
  <a class="link" style="left:292px">Lotions</a>
  <a class="link" style="left:383px">Soaps</a>
  <a class="link" style="left:727px">Body Sprays</a>
  <a class="link" style="left:856px">Wax Melts</a>
  <svg class="abs" style="left:963px;top:27px" width="24" height="26" viewBox="0 0 24 26" fill="none" stroke="#fff" stroke-width="1.8"><circle cx="12" cy="8" r="6"/><path d="M2 25c1-6 5-9 10-9s9 3 10 9"/></svg>
  <svg class="abs" style="left:1010px;top:29px" width="22" height="22" viewBox="0 0 22 22" fill="none" stroke="#fff" stroke-width="2"><circle cx="9" cy="9" r="7"/><path d="M14 14l7 7"/></svg>
  <svg class="abs" style="left:1050px;top:26px" width="32" height="28" viewBox="0 0 32 28" fill="none" stroke="#fff" stroke-width="2"><path d="M1 2h5l4 17h16l4-12H8"/><circle cx="12" cy="25" r="2"/><circle cx="24" cy="25" r="2"/></svg>
  <div class="abs" style="left:1076px;top:16px;width:20px;height:20px;border-radius:50%;background:var(--blue);font-size:11px;text-align:center;line-height:20px">0</div>
</nav>

<div class="abs hero-photo" role="img" aria-label="Flat lay of aromatherapy candles, creams, oils, salts and flowers on grey stone"></div>
<svg class="abs" style="left:0;top:600px" width="1200" height="100" viewBox="0 0 1200 100" preserveAspectRatio="none">
  <path d="M0 25 Q600 85 1200 20 L1200 100 L0 100Z" fill="var(--purple-deep)"/>
  <path d="M0 75 Q600 65 1200 32 L1200 100 L0 100Z" fill="#fff"/>
</svg>
<div class="abs brand-badge"><i></i>VELQUINT</div>
<h1 class="abs hero-title">ELEVATE YOUR CHOICES IN<br>AROMATHERAPY PRODUCTS</h1>
<p class="abs hero-sub">Lorem Ipsum is simply dummy text of the printing and<br>typesetting industry.</p>
<a class="btn" style="left:519px;top:422px;width:160px;height:48px">GET STARTED</a>

<div class="cat" style="left:-217px" role="img" aria-label="Partial category card"></div>
<div class="cat" style="left:112px" role="img" aria-label="Candles category with lit candle photo">
  <h3>Candles</h3><p>Lorem Ipsum is simply dummy text of the printing and typesetting</p>
  <a class="btn">VIEW MORE</a>
</div>
<div class="cat" style="left:445px" role="img" aria-label="Lotions category with lotion bottle photo">
  <h3>Lotions</h3><p>Lorem Ipsum is simply dummy text of the printing and</p>
  <div class="soon">Coming Soon</div>
  <a class="btn">VIEW MORE</a>
</div>
<div class="cat" style="left:780px" role="img" aria-label="Soaps category with soap bars photo">
  <h3>Soaps</h3><p>Lorem Ipsum is simply dummy text of the printing and</p>
  <div class="soon">Coming Soon</div>
  <a class="btn">VIEW MORE</a>
</div>
<div class="cat" style="left:1106px" role="img" aria-label="Next category card">
  <h3>Soaps</h3><p>Lorem Ipsum is simply dummy text</p>
  <a class="btn">VIEW MORE</a>
</div>
<div class="arrow" style="left:31px;top:874px"><svg width="14" height="14" viewBox="0 0 14 14" fill="none" stroke="#222" stroke-width="2"><path d="M9 2L4 7l5 5"/></svg></div>
<div class="arrow next" style="left:1123px;top:874px"><svg width="14" height="14" viewBox="0 0 14 14" fill="none" stroke="#6a2fd0" stroke-width="2"><path d="M5 2l5 5-5 5"/></svg></div>

<h2 class="heading" style="top:1082px">OUR PRODUCTS</h2>
<div class="arrow" style="left:31px;top:1339px"><svg width="14" height="14" viewBox="0 0 14 14" fill="none" stroke="#222" stroke-width="2"><path d="M9 2L4 7l5 5"/></svg></div>
<div class="arrow next" style="left:1123px;top:1339px"><svg width="14" height="14" viewBox="0 0 14 14" fill="none" stroke="#6a2fd0" stroke-width="2"><path d="M5 2l5 5-5 5"/></svg></div>

<div class="product" style="left:112px">
  <div class="photo" role="img" aria-label="White candle in a glass jar" style="background:linear-gradient(160deg,#f4f4f4,#d8d8d8)"></div>
  <div class="icon" style="top:21px"><svg width="22" height="20" viewBox="0 0 22 20" fill="none" stroke="#222" stroke-width="1.8"><path d="M11 18S2 12 2 6.5A4.5 4.5 0 0 1 11 4a4.5 4.5 0 0 1 9 2.5C20 12 11 18 11 18z"/></svg></div>
  <div class="icon" style="top:78px"><svg width="22" height="20" viewBox="0 0 22 20" fill="none" stroke="#222" stroke-width="1.6"><path d="M1 2h4l3 11h11l3-8H6"/><circle cx="9" cy="17" r="1.5"/><circle cx="17" cy="17" r="1.5"/></svg></div>
  <div class="label">Candle</div>
  <div class="stars">★★★★★</div>
  <div class="price"><s>$93.88</s>$54.49</div>
  <a class="btn">ADD TO CART</a>
</div>
<div class="product" style="left:452px">
  <div class="photo" role="img" aria-label="Cream pillar candle on stones"></div>
  <div class="icon" style="top:21px"><svg width="22" height="20" viewBox="0 0 22 20" fill="none" stroke="#222" stroke-width="1.8"><path d="M11 18S2 12 2 6.5A4.5 4.5 0 0 1 11 4a4.5 4.5 0 0 1 9 2.5C20 12 11 18 11 18z"/></svg></div>
  <div class="icon" style="top:78px"><svg width="22" height="20" viewBox="0 0 22 20" fill="none" stroke="#222" stroke-width="1.6"><path d="M1 2h4l3 11h11l3-8H6"/><circle cx="9" cy="17" r="1.5"/><circle cx="17" cy="17" r="1.5"/></svg></div>
  <div class="label">Candle</div>
  <div class="stars">★★★★★</div>
  <div class="price"><s>$93.88</s>$54.49</div>
  <a class="btn">ADD TO CART</a>
</div>
<div class="product" style="left:792px">
  <div class="photo" role="img" aria-label="Tall cream candle on stones" style="background:linear-gradient(160deg,#f1dfd0,#d9bda6)"></div>
  <div class="icon" style="top:21px"><svg width="22" height="20" viewBox="0 0 22 20" fill="none" stroke="#222" stroke-width="1.8"><path d="M11 18S2 12 2 6.5A4.5 4.5 0 0 1 11 4a4.5 4.5 0 0 1 9 2.5C20 12 11 18 11 18z"/></svg></div>
  <div class="icon" style="top:78px"><svg width="22" height="20" viewBox="0 0 22 20" fill="none" stroke="#222" stroke-width="1.6"><path d="M1 2h4l3 11h11l3-8H6"/><circle cx="9" cy="17" r="1.5"/><circle cx="17" cy="17" r="1.5"/></svg></div>
  <div class="label">Candle</div>
  <div class="stars">★★★★★</div>
  <div class="price"><s>$93.88</s>$54.49</div>
  <a class="btn">ADD TO CART</a>
</div>

<svg class="abs custom-bg" width="1200" height="568" viewBox="0 0 1200 568">
  <defs><linearGradient id="vaseTone" x1="0" x2="1" y1="0" y2="1"><stop offset="0" stop-color="#ecebee"/><stop offset="1" stop-color="#c9c4c0"/></linearGradient></defs>
  <path d="M0 40 Q600 -40 1200 40 L1200 540 Q600 600 0 540Z" fill="var(--grey-bg)"/>
  <path d="M560 30 Q880 0 1200 40 L1200 540 Q880 580 560 565 Q520 300 560 30Z" fill="url(#vaseTone)" role="img" aria-label="White vases with dried flowers, reed diffuser and a lit candle on a knit throw"/>
</svg>
<h2 class="abs custom-title">CUSTOMIZE YOUR<br>PRODUCT</h2>
<p class="abs custom-text">Lorem Ipsum is simply dummy text of the printing and typesetting industry. Lorem Ipsum has been the industry's standard dummy text ever since the 1500s, when an unknown printer took a galley of type and scrambled it to make a type specimen book.</p>
<a class="btn" style="left:110px;top:2074px;width:160px;height:44px">TRY NOW</a>

<h2 class="heading" style="top:2330px">OUR BENEFITS</h2>
<div class="benefit" style="left:112px">
  <div class="ico"><svg width="52" height="36" viewBox="0 0 52 36" fill="none" stroke="#333" stroke-width="1.8"><rect x="2" y="4" width="30" height="22" rx="2"/><path d="M32 12h10l8 8v6H32"/><circle cx="12" cy="29" r="4"/><circle cx="40" cy="29" r="4"/></svg></div>
  <h4>Free Shipping</h4><p>Lorem Ipsum is simply dummy text of the printing and typesetting</p>
</div>
<div class="benefit" style="left:360px">
  <div class="ico"><svg width="44" height="44" viewBox="0 0 44 44" fill="none" stroke="#333" stroke-width="1.8"><path d="M6 12l14-8 14 8v18l-14 8-14-8z"/><path d="M6 12l14 8 14-8M20 20v18"/><path d="M30 34a7 7 0 1 0 7-7"/></svg></div>
  <h4>Free Return</h4><p>Lorem Ipsum is simply dummy text of the printing and typesetting</p>
</div>
<div class="benefit" style="left:604px">
  <div class="ico"><svg width="44" height="44" viewBox="0 0 44 44" fill="none" stroke="#333" stroke-width="1.8"><circle cx="22" cy="14" r="10"/><path d="M4 32c6-4 12-4 18 0l12-6c3-1 5 2 2 4l-14 8H8"/></svg></div>
  <h4>Eco- Friendly</h4><p>Lorem Ipsum is simply dummy text of the printing and typesetting</p>
</div>
<div class="benefit" style="left:853px">
  <div class="ico"><svg width="44" height="44" viewBox="0 0 44 44" fill="none" stroke="#333" stroke-width="1.8"><path d="M8 24v-4a14 14 0 0 1 28 0v4"/><rect x="4" y="22" width="8" height="12" rx="3"/><rect x="32" y="22" width="8" height="12" rx="3"/><path d="M36 34c0 4-6 6-12 6"/><circle cx="17" cy="26" r="1"/><circle cx="22" cy="26" r="1"/><circle cx="27" cy="26" r="1"/></svg></div>
  <h4>Support 24/7</h4><p>Lorem Ipsum is simply dummy text of the printing and typesetting</p>
</div>

<h2 class="heading" style="top:2758px">OUR TESTIMONIALS</h2>
<div class="review" style="left:110px">
  <p>Lorem Ipsum is simply dummy text of the printing and typesetting industry. Lorem Ipsum has been the industry's standard dummy text</p>
  <hr><div class="avatar" role="img" aria-label="Client portrait"></div>
  <span class="name">Darin</span><span class="role">Client</span><span class="stars">★★★★★</span><span class="src">Revio</span>
</div>
<div class="review" style="left:443px">
  <p style="top:30px">Lorem Ipsum is simply dummy text of the printing and typesetting industry. Lorem Ipsum has been the industry's standard</p>
  <hr><div class="avatar" role="img" aria-label="Client portrait"></div>
  <span class="name">Silas</span><span class="role">Client</span><span class="stars">★★★★★</span><span class="src">Revio</span>
</div>
<div class="review" style="left:778px">
  <p>Lorem Ipsum is simply dummy text of the printing and typesetting industry. Lorem Ipsum has been the industry's standard dummy text</p>
  <hr><div class="avatar" role="img" aria-label="Client portrait"></div>
  <span class="name">Teo</span><span class="role">Client</span><span class="stars">★★★★★</span><span class="src">Revio</span>
</div>
<div class="dot" style="left:569px;top:3193px;width:19px;height:19px;background:var(--blue);border:3px solid #cfe6fb"></div>
<div class="dot" style="left:598px"></div>
<div class="dot" style="left:621px"></div>

<svg class="abs follow-bg" width="1200" height="590" viewBox="0 0 1200 590">
  <defs><linearGradient id="followTone" x1="0" x2="0" y1="0" y2="1"><stop offset="0" stop-color="#7a3ad6"/><stop offset="1" stop-color="#6a2ec8"/></linearGradient></defs>
  <path d="M0 60 Q600 -50 1200 60 L1200 590 L0 590Z" fill="url(#followTone)"/>
</svg>
<h2 class="abs follow-title">FOLLOW US ON <span style="display:inline-block;width:30px;height:30px;border:3px solid #fff;border-radius:7px;vertical-align:-3px;margin-left:6px"></span></h2>
<div class="shot" style="left:112px;width:234px;background:linear-gradient(160deg,#c7a685,#7b5a40)" role="img" aria-label="Candle on a wooden tray"></div>
<div class="shot" style="left:360px;width:236px;background:linear-gradient(160deg,#5b8ae0,#3a6ad6)" role="img" aria-label="Bath products in blue light"></div>
<div class="shot" style="left:604px;width:234px;background:linear-gradient(160deg,#d8c4ae,#8d6f55)" role="img" aria-label="Group of lit candles on woven mat"></div>
<div class="shot" style="left:853px;width:235px;background:linear-gradient(160deg,#8a6a55,#e8ddd4)" role="img" aria-label="Candles and amber bottles"></div>
<a class="btn" style="left:518px;top:3791px;width:157px;height:46px;background:var(--blue);font-family:'Poppins',sans-serif;font-size:15px">FOLLOW US</a>

<footer class="abs footer"></footer>
<h2 class="abs news-title">Subscribe To Our Newsletter</h2>
<div class="field" style="left:112px;width:273px">Name</div>
<div class="field" style="left:409px;width:481px">Enter Your Email</div>
<a class="btn" style="left:909px;top:4077px;width:179px;height:46px;background:var(--blue);font-family:'Poppins',sans-serif;font-size:16px;font-weight:600">SUBSCRIBE</a>
<div class="rule" style="top:4181px"></div>

<div class="abs" style="left:156px;top:4227px;width:142px;height:142px;border-radius:50%;background:#000;border:1px solid #2a2a2a;display:flex;flex-direction:column;align-items:center;justify-content:center;font-family:'Montserrat',sans-serif;font-weight:700;font-size:16px;letter-spacing:2px;color:#b89af2"><i style="display:block;width:44px;height:44px;border-radius:50%;background:var(--purple);margin-bottom:8px"></i>VELQUINT</div>
<span class="social" style="left:147px"></span>
<span class="social" style="left:195px"></span>
<span class="social" style="left:243px"></span>
<span class="social" style="left:293px"></span>

<h4 class="col-title" style="left:427px">QUICK LINKS</h4>
<a class="col-link" style="left:427px;top:4281px"><b>›</b>Home</a>
<a class="col-link" style="left:427px;top:4314px"><b>›</b>About Us</a>
<a class="col-link" style="left:427px;top:4348px"><b>›</b>Our Product</a>
<a class="col-link" style="left:427px;top:4381px"><b>›</b>Contact Us</a>

<h4 class="col-title" style="left:659px">HELP LINKS</h4>
<a class="col-link" style="left:659px;top:4281px"><b>›</b>FAQ</a>
<a class="col-link" style="left:659px;top:4314px"><b>›</b>Terms of use</a>
<a class="col-link" style="left:659px;top:4348px"><b>›</b>Privacy Policy</a>
<a class="col-link" style="left:659px;top:4381px"><b>›</b>Support Links</a>
<a class="col-link" style="left:659px;top:4415px"><b>›</b>Conditions</a>

<h4 class="col-title" style="left:872px">CONTACT US</h4>
<svg class="abs" style="left:874px;top:4284px" width="28" height="28" viewBox="0 0 28 28"><circle cx="14" cy="14" r="14" fill="#fff"/><path d="M14 6a5 5 0 0 0-5 5c0 4 5 10 5 10s5-6 5-10a5 5 0 0 0-5-5z" fill="#000"/><circle cx="14" cy="11" r="2" fill="#fff"/></svg>
<span class="col-link" style="left:916px;top:4281px;line-height:28px">Velquint<br>United States</span>
<svg class="abs" style="left:874px;top:4346px" width="28" height="28" viewBox="0 0 28 28"><circle cx="14" cy="14" r="14" fill="#fff"/><path d="M9 7l3 0 1 4-2 1c1 2 3 4 5 5l1-2 4 1 0 3c-8 1-13-5-12-12z" fill="#000"/></svg>
<span class="col-link" style="left:916px;top:4351px">+1 555 014 2270</span>
<svg class="abs" style="left:874px;top:4398px" width="28" height="28" viewBox="0 0 28 28"><circle cx="14" cy="14" r="14" fill="#fff"/><rect x="7" y="9" width="14" height="10" rx="1" fill="#000"/><path d="M7 10l7 5 7-5" stroke="#fff" stroke-width="1.2" fill="none"/></svg>
<span class="col-link" style="left:916px;top:4403px">info@velquint.com</span>

<div class="rule" style="top:4484px"></div>
<p class="abs" style="left:110px;top:4519px;font-size:14px;color:#fff">Copyrights@2024. Velquint .All Rights Reserved</p>
<span class="pay" style="left:659px;background:#8e86f4"></span>
<span class="pay" style="left:699px;background:#3e86d6"></span>
<span class="pay" style="left:738px"></span>
<span class="pay" style="left:778px"></span>
<span class="pay" style="left:817px"></span>
<span class="pay" style="left:857px"></span>
<span class="pay" style="left:896px"></span>
<span class="pay" style="left:936px;background:#5b6bf0"></span>
<span class="pay" style="left:975px;background:#3d8ee0"></span>
<span class="pay" style="left:1015px"></span>
<span class="pay" style="left:1054px"></span>

</body>
</html>
```